Redesign Website - Current one too plain

The description is in the uploaded file. Please let me know if you need any more information. I'd prefer it if someone could implement the design to a WordPress site but the best design will win, regardless.
I would like the forms to look nice as well
UPDATE:
I don't think we can use the images that I provided, I think they make the site look a bit 'cheap' and I really don't know how to replace them. One thought I have had is to make the "Simple, Unique, Effective" a second feature on the right side of the page with the search on the left
Target Market(s)
Small companies, private sellers of cars and people who rent their caravan/holiday home out
Industry/Entity Type
Advertising
Number of Pages Required
3 page
Colors
Designer to choose colors to be used in the design.
Look and feel
Each slider illustrates characteristics of the customer's brand and the style your logo design should communicate.

```html
<!DOCTYPE html>
<html lang="en">
<head>
<meta charset="utf-8">
<title>Plateo.com – Advertise with a memorable code</title>
<link href="https://fonts.googleapis.com/css2?family=Roboto:wght@300;400;500;700&display=swap" rel="stylesheet">
<style>
:root{
  --dark:#2b2b2b;
  --darker:#222222;
  --lime:#e2ff00;
  --ink:#2e2e2e;
  --pill:#d9d9d9;
  --muted:#7a7a7a;
  --white:#ffffff;
  --star:#c9b800;
}
*{box-sizing:border-box;margin:0;padding:0}
html,body{width:1200px;height:2517px;overflow:hidden}
body{font-family:'Roboto',sans-serif;color:var(--ink);background:var(--white);position:relative}
a{color:inherit;text-decoration:none}
.abs{position:absolute}

/* hero */
.hero{position:absolute;left:0;top:0;width:1200px;height:703px;background:var(--dark);overflow:hidden}
.hero-photo{position:absolute;left:105px;top:135px;width:980px;height:520px;border-radius:40px;
  background:radial-gradient(ellipse at 50% 45%,#4a4a4a 0%,#3a3a3a 45%,var(--dark) 75%)}
.logo{position:absolute;display:flex;align-items:center;gap:14px;font-weight:500;color:var(--lime);font-size:36px;letter-spacing:6px}
.logo .dot{width:30px;height:30px;border-radius:50%;background:var(--lime)}
.logo small{font-size:26px;letter-spacing:3px}
.nav{position:absolute;left:519px;top:36px;display:flex;gap:26px;color:var(--white);font-size:16px}
.nav span.sep{opacity:.9}
.btn{display:inline-flex;align-items:center;justify-content:center;gap:10px;border-radius:30px;font-weight:500;font-size:16px}
.btn-lime{background:var(--lime);color:var(--ink)}
.btn-dark{background:var(--ink);color:var(--lime)}
.login{position:absolute;left:953px;top:26px;width:135px;height:43px}
.code{position:absolute;left:0;width:1200px;top:158px;text-align:center;color:var(--lime);font-weight:700;font-size:150px;line-height:1;letter-spacing:4px}
.chev{position:absolute}
.tabs{position:absolute;left:379px;top:355px;display:flex;gap:9px}
.tab{width:142px;height:45px;border-radius:25px;background:var(--pill);display:flex;align-items:center;justify-content:center;gap:12px;font-weight:500;font-size:16px;color:var(--ink)}
.search{position:absolute;left:379px;top:427px;width:443px;height:46px;border-radius:25px;background:var(--lime);display:flex;align-items:center;padding-left:35px;font-weight:500;font-size:16px}
.search .go{position:absolute;right:3px;top:3px;width:40px;height:40px;border-radius:50%;background:var(--ink);display:flex;align-items:center;justify-content:center}
.perks{position:absolute;left:0;width:1200px;top:505px;display:flex;justify-content:center;gap:26px;color:var(--white);font-size:16px;font-weight:500}
.perks span{display:flex;align-items:center;gap:9px}
.perks i{width:12px;height:12px;border-radius:50%;background:var(--lime);display:block}
.advertise{position:absolute;left:482px;top:556px;width:237px;height:45px}

/* features */
.card{position:absolute;top:795px;width:302px;height:313px;background:var(--white);border-radius:80px 0 80px 0;box-shadow:0 10px 40px rgba(0,0,0,.09);text-align:center}
.card::before{content:"";position:absolute;inset:8px;border:2px dotted #c8c8c8;border-radius:74px 0 74px 0}
.card .ico{position:relative;margin:40px auto 0;width:104px;height:104px;border-radius:50%;border:3px solid #e0e0e0;display:flex;align-items:center;justify-content:center}
.card .ico div{width:94px;height:94px;border-radius:50%;background:var(--dark);display:flex;align-items:center;justify-content:center}
.card h3{margin-top:19px;font-size:18px;font-weight:500}
.card p{margin:12px auto 0;width:240px;font-size:15.5px;font-weight:300;line-height:22px;color:#3a3a3a}
.card .more{display:inline-flex;align-items:center;gap:8px;margin-top:19px;font-weight:500;font-size:15px}

/* create */
.create{position:absolute;left:0;top:1208px;width:1200px;height:307px;background:var(--lime);text-align:center}
.create h2{margin-top:67px;font-size:35px;font-weight:500;color:#3a3a3a}
.ticks{display:flex;justify-content:center;gap:44px;margin-top:22px;font-size:16px;font-weight:300;color:#3a3a3a}
.ticks span{display:flex;align-items:center;gap:12px}
.create .btn{margin-top:26px;width:194px;height:45px}

/* testimonials */
.testi-title{position:absolute;left:0;width:1200px;top:1595px;text-align:center;font-size:35px;font-weight:500;color:#3a3a3a}
.quote{position:absolute;top:1675px;width:469px;height:243px;background:var(--white);box-shadow:0 6px 30px rgba(0,0,0,.07);border-radius:6px;padding:20px 31px}
.stars{display:flex;gap:4px}
.quote p{margin-top:14px;font-size:15.5px;font-weight:300;line-height:28.5px;color:var(--muted);text-align:justify}
.author{display:flex;align-items:center;gap:20px;margin-top:9px;font-size:17px;font-weight:500}
.avatar{width:54px;height:54px;border-radius:50%;background:linear-gradient(135deg,#c7b49a,#8a7a68)}

/* footer */
.footer{position:absolute;left:0;top:2003px;width:1200px;height:442px;background:var(--dark);color:var(--white)}
.field{position:absolute;top:73px;width:237px;height:46px;border-radius:25px;background:var(--pill);color:#444;font-size:14px;display:flex;align-items:center;padding-left:24px}
.submit{position:absolute;left:852px;top:73px;width:236px;height:46px}
.rule{position:absolute;left:111px;top:175px;width:977px;height:1px;background:#444}
.col{position:absolute;top:202px;font-size:14px}
.col h4{font-size:18px;font-weight:500;margin-bottom:20px}
.col li{list-style:none;line-height:26px}
.contact-item{display:flex;gap:12px;margin-bottom:12px;line-height:19px}
.contact-item b{display:block;font-size:12px;font-weight:500}
.top-btn{position:absolute;left:1130px;top:375px;width:36px;height:36px;border-radius:50%;background:var(--lime);display:flex;align-items:center;justify-content:center}
.bottom{position:absolute;left:0;top:2445px;width:1200px;height:72px;background:var(--lime);display:flex;align-items:center;justify-content:center;font-size:15px;color:#3a3a3a}
</style>
</head>
<body>

<header class="hero">
  <div class="hero-photo" role="img" aria-label="Faded photo of a car, a caravan and a van showing code plates"></div>
  <div class="logo" style="left:111px;top:26px"><span class="dot"></span><span>PLATEO<small>.com</small></span></div>
  <nav class="nav"><a>Home</a><span class="sep">|</span><a>Advertise</a><span class="sep">|</span><a>Contact</a><span class="sep">|</span><a>Register</a></nav>
  <a class="btn btn-lime login">Login
    <svg width="11" height="12" viewBox="0 0 11 12"><rect x="1" y="5" width="9" height="7" rx="1" fill="#2e2e2e"/><path d="M3 5V3.5a2.5 2.5 0 0 1 5 0V5" stroke="#2e2e2e" stroke-width="1.6" fill="none"/></svg></a>

  <svg class="chev" style="left:566px;top:160px" width="14" height="10"><path d="M2 8l5-5 5 5" stroke="#fff" stroke-width="2" fill="none"/></svg>
  <svg class="chev" style="left:656px;top:160px" width="14" height="10"><path d="M2 8l5-5 5 5" stroke="#fff" stroke-width="2" fill="none"/></svg>
  <div class="code">A1</div>
  <svg class="chev" style="left:566px;top:305px" width="14" height="10"><path d="M2 2l5 5 5-5" stroke="#fff" stroke-width="2" fill="none"/></svg>
  <svg class="chev" style="left:656px;top:305px" width="14" height="10"><path d="M2 2l5 5 5-5" stroke="#fff" stroke-width="2" fill="none"/></svg>

  <div class="tabs">
    <div class="tab">Car <svg width="24" height="14" viewBox="0 0 24 14"><path d="M2 10V7l3-1 3-4h8l4 4 2 1v3H2z" stroke="#555" fill="none" stroke-width="1.2"/><circle cx="7" cy="11" r="2" fill="#d9d9d9" stroke="#555"/><circle cx="17" cy="11" r="2" fill="#d9d9d9" stroke="#555"/></svg></div>
    <div class="tab">Caravan <svg width="22" height="14" viewBox="0 0 22 14"><rect x="1" y="1" width="17" height="9" rx="1" stroke="#555" fill="none" stroke-width="1.2"/><rect x="4" y="3" width="4" height="3" stroke="#555" fill="none"/><rect x="10" y="3" width="4" height="3" stroke="#555" fill="none"/><circle cx="7" cy="11.5" r="2" fill="#d9d9d9" stroke="#555"/><path d="M18 8h3" stroke="#555"/></svg></div>
    <div class="tab">Company <svg width="12" height="16" viewBox="0 0 12 16"><rect x="1" y="1" width="10" height="14" stroke="#555" fill="none" stroke-width="1.2"/><path d="M4 4h1M7 4h1M4 7h1M7 7h1M4 10h1M7 10h1" stroke="#555"/></svg></div>
  </div>
  <div class="search">Search
    <div class="go"><svg width="14" height="14" viewBox="0 0 14 14"><circle cx="6" cy="6" r="4" stroke="#fff" stroke-width="2" fill="none"/><path d="M9 9l3.5 3.5" stroke="#fff" stroke-width="2"/></svg></div>
  </div>
  <div class="perks"><span><i></i>Simple</span><span><i></i>Unique</span><span><i></i>Effective</span></div>
  <a class="btn btn-lime advertise">Advertise your company
    <svg width="14" height="14" viewBox="0 0 14 14"><circle cx="7" cy="7" r="6.5" fill="#2e2e2e"/><path d="M5 7h4M7 5l2 2-2 2" stroke="#e2ff00" stroke-width="1.6" fill="none"/></svg></a>
</header>

<section class="features">
  <article class="card" style="left:122px">
    <div class="ico"><div><svg width="50" height="50" viewBox="0 0 50 50"><path d="M8 42l20-20" stroke="#e2ff00" stroke-width="5" stroke-linecap="round"/><path d="M33 8l3 7 7 1-5 5 1 7-6-4-6 4 1-7-5-5 7-1z" fill="#e2ff00"/></svg></div></div>
    <h3>Simple</h3>
    <p>Create your advert and display your code</p>
    <a class="more">READ MORE <svg width="14" height="14" viewBox="0 0 14 14"><circle cx="7" cy="7" r="6.5" fill="#2e2e2e"/><path d="M5 7h4M7 5l2 2-2 2" stroke="#fff" stroke-width="1.6" fill="none"/></svg></a>
  </article>
  <article class="card" style="left:449px">
    <div class="ico"><div><svg width="50" height="50" viewBox="0 0 50 50" fill="none" stroke="#e2ff00" stroke-width="3" stroke-linecap="round"><path d="M10 30a15 15 0 0 1 30-10"/><path d="M15 34a10 10 0 0 1 20-8"/><path d="M20 38a5 5 0 0 1 10-6"/><path d="M14 14a18 18 0 0 1 24 2"/><path d="M40 26v6"/></svg></div></div>
    <h3>Unique</h3>
    <p>customers find you by an easy-to-remember code</p>
    <a class="more">READ MORE <svg width="14" height="14" viewBox="0 0 14 14"><circle cx="7" cy="7" r="6.5" fill="#2e2e2e"/><path d="M5 7h4M7 5l2 2-2 2" stroke="#fff" stroke-width="1.6" fill="none"/></svg></a>
  </article>
  <article class="card" style="left:776px">
    <div class="ico"><div><svg width="50" height="50" viewBox="0 0 50 50" fill="none" stroke="#e2ff00" stroke-width="4"><circle cx="24" cy="26" r="18"/><circle cx="24" cy="26" r="10"/><circle cx="24" cy="26" r="3" fill="#e2ff00"/><path d="M24 26l16-16" stroke-width="3"/></svg></div></div>
    <h3>Effective</h3>
    <p>customers are directed to you and not a list of your competitors</p>
    <a class="more">READ MORE <svg width="14" height="14" viewBox="0 0 14 14"><circle cx="7" cy="7" r="6.5" fill="#2e2e2e"/><path d="M5 7h4M7 5l2 2-2 2" stroke="#fff" stroke-width="1.6" fill="none"/></svg></a>
  </article>
</section>

<section class="create">
  <h2>Create Your Advert</h2>
  <div class="ticks">
    <span><svg width="14" height="14" viewBox="0 0 14 14"><circle cx="7" cy="7" r="6.5" fill="#2e2e2e"/><path d="M4 7l2 2 4-4" stroke="#e2ff00" stroke-width="1.6" fill="none"/></svg>Free to advertise</span>
    <span><svg width="14" height="14" viewBox="0 0 14 14"><circle cx="7" cy="7" r="6.5" fill="#2e2e2e"/><path d="M4 7l2 2 4-4" stroke="#e2ff00" stroke-width="1.6" fill="none"/></svg>Free graphics to print and display</span>
    <span><svg width="14" height="14" viewBox="0 0 14 14"><circle cx="7" cy="7" r="6.5" fill="#2e2e2e"/><path d="M4 7l2 2 4-4" stroke="#e2ff00" stroke-width="1.6" fill="none"/></svg>Weatherproof vinyl graphics available</span>
  </div>
  <a class="btn btn-dark">Login or Register <svg width="14" height="14" viewBox="0 0 14 14"><circle cx="7" cy="7" r="6.5" fill="#e2ff00"/><path d="M5 7h4M7 5l2 2-2 2" stroke="#2e2e2e" stroke-width="1.6" fill="none"/></svg></a>
</section>

<section class="testimonials">
  <h2 class="testi-title">Our Testimonilas</h2>
  <article class="quote" style="left:118px">
    <div class="stars">
      <svg width="94" height="14" viewBox="0 0 94 14" fill="#c9b800"><g id="s"><path d="M7 0l2 5h5l-4 3 2 5-5-3-5 3 2-5-4-3h5z"/></g><use href="#s" x="19"/><use href="#s" x="38"/><use href="#s" x="57"/><use href="#s" x="76"/></svg>
    </div>
    <p>Lorem ipsum dolor sit amet, consectetur adipiscing elit, sed do eiusmod tempor incididunt ut labore et dolore magna aliqua enim minim veniam nostrud exercitation ullamco laboris nisi aliquip ex ea commodo consequat.</p>
    <div class="author"><div class="avatar" role="img" aria-label="Customer portrait"></div>Mara Lentz</div>
  </article>
  <article class="quote" style="left:612px">
    <div class="stars">
      <svg width="94" height="14" viewBox="0 0 94 14" fill="#c9b800"><use href="#s"/><use href="#s" x="19"/><use href="#s" x="38"/><use href="#s" x="57"/><use href="#s" x="76"/></svg>
    </div>
    <p>Lorem ipsum dolor sit amet, consectetur adipiscing elit, sed do eiusmod tempor incididunt ut labore et dolore magna aliqua enim minim veniam nostrud exercitation ullamco laboris nisi aliquip ex ea commodo consequat.</p>
    <div class="author"><div class="avatar" role="img" aria-label="Customer portrait"></div>Mara Lentz</div>
  </article>
</section>

<footer class="footer">
  <div class="field" style="left:111px">Enter Name</div>
  <div class="field" style="left:358px">Enter Email</div>
  <div class="field" style="left:605px">Message</div>
  <a class="btn btn-lime submit">Submit Now <svg width="14" height="14" viewBox="0 0 14 14"><circle cx="7" cy="7" r="6.5" fill="#2e2e2e"/><path d="M5 7h4M7 5l2 2-2 2" stroke="#e2ff00" stroke-width="1.6" fill="none"/></svg></a>
  <div class="rule"></div>

  <div class="logo" style="left:108px;top:202px;font-size:32px"><span class="dot"></span><span>PLATEO<small>.com</small></span></div>

  <div class="col" style="left:453px"><h4>Quick Links</h4><ul><li>Home</li><li>Advertise</li><li>Contact</li><li>Register</li></ul></div>
  <div class="col" style="left:657px"><h4>About Company</h4><ul><li>Terms of Use</li><li>Terms &amp; Condition</li><li>News</li><li>Privacy Policy</li><li>FAQ</li></ul></div>
  <div class="col" style="left:908px"><h4>Contact Us</h4>
    <div class="contact-item"><svg width="10" height="14" viewBox="0 0 10 14"><path d="M5 0a5 5 0 0 1 5 5c0 4-5 9-5 9S0 9 0 5a5 5 0 0 1 5-5z" fill="#e2ff00"/><circle cx="5" cy="5" r="2" fill="#2b2b2b"/></svg><div><b>Location</b>177 Lorem ipsum dolor sit<br>consectetur adipiscing el</div></div>
    <div class="contact-item"><svg width="13" height="13" viewBox="0 0 13 13"><path d="M2 0l3 3-1.5 2a8 8 0 0 0 4.5 4.5L10 8l3 3-2 2C5 13 0 8 0 2z" fill="#e2ff00"/></svg><div><b>Phone</b>+1 888 888 8888</div></div>
    <div class="contact-item"><svg width="15" height="11" viewBox="0 0 15 11"><rect width="15" height="11" rx="1" fill="#e2ff00"/><path d="M1 1l6.5 5L14 1" stroke="#2b2b2b" fill="none"/></svg><div><b>Email</b>info@plateo.com</div></div>
  </div>
  <div class="top-btn"><svg width="12" height="8" viewBox="0 0 12 8"><path d="M1 7l5-5 5 5" stroke="#2e2e2e" stroke-width="2" fill="none"/></svg></div>
</footer>

<div class="bottom">2023 Copyright - Plateo &nbsp;|&nbsp; All Rights Reserved &nbsp;|</div>
</body>
</html>
```